BOLD & MINIMALIST DESIGN NEEDED

We want a very bold but minimalistic business card design that is impactful and utilizes both sides of the business card. Our current logo is included for your use.

We want bold fonts and good use of negative space. We don't want the logo to overpower the design.

Target Market(s)

Professionals who are building new commercial buildings.

Industry/Entity Type

Construction

Contact Information for Business Card

Name, Title, email, office phone, cell phone, website

Font styles to use
Serif
Sans Serif

Requirements
Must have
• Bold design!

```html
<!DOCTYPE html>
<html lang="en">
<head>
<meta charset="utf-8">
<title>Quarrowind Build – Business Card</title>
<link rel="stylesheet" href="https://fonts.googleapis.com/css2?family=Tinos:wght@400;700&display=swap">
<style>
  :root {
    --backdrop: #d3f8f8;
    --card: #ffffff;
    --green: #7cff12;
    --ink: #111111;
  }
  * { margin: 0; padding: 0; box-sizing: border-box; }
  html, body { width: 1200px; height: 1200px; overflow: hidden; background: var(--backdrop); }
  .canvas { position: relative; width: 1200px; height: 1200px; }
  .card {
    position: absolute; width: 660px; height: 377px;
    background: var(--card); overflow: hidden;
    font-family: "Tinos", "Times New Roman", serif; color: var(--ink);
  }
  .card-front { left: 291px; top: 214px; }
  .card-back { left: 284px; top: 662px; }
  .card-shapes { position: absolute; inset: 0; width: 100%; height: 100%; }
  .card-shapes .band { fill: var(--green); }
  .brand-name {
    position: absolute; font-weight: 700; text-transform: uppercase;
    white-space: nowrap; transform: translate(-50%, -50%); line-height: 1;
  }
  .card-front .brand-name { left: 320px; top: 183px; font-size: 36px; letter-spacing: 2px; }
  .card-back .brand-name { left: 532px; top: 226px; font-size: 19px; letter-spacing: 1px; }
  .holder-name {
    position: absolute; left: 36px; top: 70px;
    font-size: 28px; font-weight: 700; letter-spacing: 0.5px; line-height: 1.1;
  }
  .holder-post {
    position: absolute; left: 43px; top: 106px;
    font-size: 19px; font-weight: 400; line-height: 1.1;
  }
  .contact-list { position: absolute; left: 36px; top: 0; list-style: none; }
  .contact-item {
    position: absolute; left: 0; display: flex; align-items: center;
    font-size: 17.5px; font-weight: 700; white-space: nowrap; transform: translateY(-50%);
  }
  .contact-icon { width: 25px; height: 25px; margin-right: 14px; flex: none; }
  .contact-icon .fill { fill: var(--green); }
  .contact-icon .stroke { fill: none; stroke: var(--green); stroke-width: 2; }
  .contact-icon .cut { fill: #fff; }
  .contact-icon .cut-line { fill: none; stroke: #fff; stroke-width: 1.6; stroke-linecap: round; }
  .divider {
    position: absolute; left: 336px; top: 93px; width: 3px; height: 201px;
    background: var(--green);
  }
</style>
</head>
<body>
<main class="canvas">

  <section class="card card-front" aria-label="Card front">
    <svg class="card-shapes" viewBox="0 0 1063 607" preserveAspectRatio="none" aria-hidden="true">
      <rect class="band" x="44" y="0" width="24" height="607"/>
      <polygon class="band" points="68,0 101,0 101,330 68,303"/>
      <polygon class="band" points="78,330 128,370 132,607 80,607"/>
      <rect class="band" x="993" y="0" width="26" height="607"/>
      <polygon class="band" points="958,0 993,0 993,303 958,333"/>
      <polygon class="band" points="982,325 934,372 932,607 982,607"/>
    </svg>
    <p class="brand-name">Quarrowind Build</p>
  </section>

  <section class="card card-back" aria-label="Card back">
    <svg class="card-shapes" viewBox="0 0 1063 607" preserveAspectRatio="none" aria-hidden="true">
      <polygon class="band" points="0,0 1063,0 1063,27 533,27 562,60 0,60"/>
      <polygon class="band" points="559,36 1063,40 1063,84 603,84"/>
      <polygon class="band" points="0,521 464,521 507,568 0,564"/>
      <polygon class="band" points="0,607 1063,607 1063,543 503,543 531,577 0,577"/>
    </svg>

    <h1 class="holder-name">YOUR NAME</h1>
    <p class="holder-post">YOUR POST</p>

    <ul class="contact-list">
      <li class="contact-item" style="top:184px">
        <svg class="contact-icon" viewBox="0 0 24 24" aria-hidden="true">
          <circle class="fill" cx="12" cy="12" r="12"/>
          <path class="cut" d="M5.5 10.5c0-2 3-3.2 6.5-3.2s6.5 1.2 6.5 3.2v1h-3v-1.6h-7v1.6h-3z"/>
          <rect class="cut" x="7.5" y="12" width="9" height="5" rx="1"/>
          <circle class="fill" cx="12" cy="14.5" r="1.3"/>
        </svg>
        Office Phone
      </li>
      <li class="contact-item" style="top:219px">
        <svg class="contact-icon" viewBox="0 0 24 24" aria-hidden="true">
          <circle class="fill" cx="12" cy="12" r="12"/>
          <path class="cut" d="M8 5.5l2.3 3-1.3 1.6c.8 1.9 2.2 3.3 4.1 4.2l1.6-1.3 3 2.3-1.6 2.4c-4.8-.3-9.5-5-9.9-9.9z"/>
        </svg>
        Cell Phone
      </li>
      <li class="contact-item" style="top:250px">
        <svg class="contact-icon" viewBox="0 0 24 24" aria-hidden="true">
          <rect class="fill" x="0" y="3" width="24" height="18" rx="3"/>
          <path class="cut-line" d="M5 7l7 4.5 7-4.5"/>
        </svg>
        Your Email Address
      </li>
      <li class="contact-item" style="top:282px">
        <svg class="contact-icon" viewBox="0 0 24 24" aria-hidden="true">
          <circle class="stroke" cx="12" cy="12" r="10.5"/>
          <ellipse class="stroke" cx="12" cy="12" rx="4.5" ry="10.5"/>
          <line class="stroke" x1="1.5" y1="12" x2="22.5" y2="12"/>
          <line class="stroke" x1="12" y1="1.5" x2="12" y2="22.5"/>
        </svg>
        Your website Address
      </li>
    </ul>

    <div class="divider" aria-hidden="true"></div>
    <p class="brand-name">Quarrowind Build</p>
  </section>

</main>
</body>
</html>
```